Holistic Financial Planning Practice

I need a business card design and logo for my Financial Planning Practice(Vorn Financial Planning).

Vorn(Vigour, Openness, Reliability and Nuance) Financial Planning provides service to both individuals, companies, self managed super funds on wide range of advice. Vorn Financial Planning is licensed through TRV.

I have attached an existing business card which needs up-dating

Vorn's webpage provides a good overview of what I do which is www.vornfp-example.com.au

All the TRV branding needs to be included, including 'Vorn Financial Planning is an Authorised Representative of TRV Wealth Advisory Pty Limited ABN 71823 904 526 ACN 823 904 526'

An idea.......At Vorn It's the sense that make the dollars.

Vorn Financial Planning, Doran Fitchley MFS(FP), B.Bus, ADFS ; Suite 304, Level 3, 57 Tindall Street Corrandale QLD 4999 Australia
Ph: 02 9730 4165 Fax 02 9247 3019 Mobile 04713 62091 Email doran@vornfp-example.com.au Web www.vornfp-example.com.au

```html
<!DOCTYPE html>
<html lang="en">
<head>
<meta charset="utf-8">
<title>Vorn Financial Planning – Business Card</title>
<link rel="stylesheet" href="https://fonts.googleapis.com/css2?family=Tinos:wght@400;700&display=swap">
<style>
  :root {
    --backdrop: #2c2c2d;
    --card: #ffffff;
    --band: #8dbbe3;
    --navy: #1d4f9e;
    --brand-blue: #1a5aa8;
    --text-blue: #2b80c8;
    --band-text: #f4f8fc;
  }
  * { margin: 0; padding: 0; box-sizing: border-box; }
  html, body {
    width: 1200px; height: 800px; overflow: hidden;
    background: var(--backdrop);
    font-family: "Tinos", "Times New Roman", serif;
  }
  .card {
    position: absolute; left: 80px; top: 85px;
    width: 1040px; height: 630px;
    background: var(--card);
    border-radius: 4px;
    overflow: hidden;
    box-shadow: 0 6px 18px rgba(0,0,0,.45);
  }
  .band {
    position: absolute; left: 0; right: 0; top: 150px; height: 130px;
    background: var(--band);
  }
  .brand {
    position: absolute; left: 58px; top: 82px;
    display: flex; align-items: center; gap: 16px;
  }
  .brand-dot {
    width: 44px; height: 44px; border-radius: 50%;
    background: var(--brand-blue);
  }
  .brand-name {
    color: var(--brand-blue);
    font-size: 30px; letter-spacing: 3px; font-weight: 400;
  }
  .holder {
    position: absolute; right: 44px; top: 160px; text-align: right;
  }
  .holder-name {
    color: var(--navy); font-weight: 700; font-size: 31px; letter-spacing: 2px;
  }
  .holder-meta {
    color: var(--band-text); font-size: 19px; letter-spacing: 2.5px; line-height: 1.45;
  }
  .contacts {
    position: absolute; left: 88px; bottom: 60px;
    list-style: none;
  }
  .contacts li {
    display: flex; align-items: center; gap: 18px;
    color: var(--text-blue); font-size: 27px; letter-spacing: 3px; line-height: 44px;
  }
  .contacts svg { width: 34px; height: 30px; fill: var(--navy); flex: none; }
  .address {
    position: absolute; right: 44px; top: 340px;
    display: flex; gap: 24px; align-items: flex-start;
  }
  .address svg { width: 26px; height: 36px; fill: var(--navy); margin-top: 26px; }
  .address p {
    color: var(--text-blue); font-size: 27px; letter-spacing: 3px; line-height: 40px; text-align: right;
  }
</style>
</head>
<body>
<main class="card">
  <div class="band"></div>

  <div class="brand">
    <span class="brand-dot"></span>
    <span class="brand-name">VORN FINANCIAL PLANNING</span>
  </div>

  <div class="holder">
    <div class="holder-name">Doran Fitchley</div>
    <div class="holder-meta">MFS(FP), B.Bus ADFS<br>Financial Planner/Principal</div>
  </div>

  <ul class="contacts">
    <li><svg viewBox="0 0 34 30" aria-hidden="true"><path d="M2 10c0-5 30-5 30 0v3h-8v-3H10v3H2z"/><path d="M8 14h18l5 13H3z"/><circle cx="17" cy="20" r="3" fill="#fff"/></svg>02 9730 4165</li>
    <li><svg viewBox="0 0 34 30" aria-hidden="true"><rect x="3" y="10" width="8" height="18" rx="2"/><rect x="12" y="12" width="20" height="16" rx="2"/><rect x="15" y="2" width="14" height="10"/><rect x="16" y="16" width="3" height="3" fill="#fff"/><rect x="21" y="16" width="3" height="3" fill="#fff"/><rect x="26" y="16" width="3" height="3" fill="#fff"/><rect x="16" y="21" width="3" height="3" fill="#fff"/><rect x="21" y="21" width="3" height="3" fill="#fff"/><rect x="26" y="21" width="3" height="3" fill="#fff"/></svg>02 9247 3019</li>
    <li><svg viewBox="0 0 34 30" aria-hidden="true"><path d="M10 2l5 6-3 4c2 5 5 8 10 10l4-3 6 5-3 5C18 29 5 16 5 5z"/></svg>04713 62091</li>
    <li><svg viewBox="0 0 34 30" aria-hidden="true"><path d="M2 6h30v20H2z"/><path d="M2 6l15 12L32 6" fill="none" stroke="#fff" stroke-width="2"/></svg>doran@vornfp-example.com.au</li>
    <li><svg viewBox="0 0 34 30" aria-hidden="true"><path d="M2 3h30v19H2z"/><path d="M5 6h24v13H5z" fill="#fff"/><path d="M13 22h8v4h4v2H9v-2h4z"/></svg>www.vornfp-example.com.au</li>
  </ul>

  <div class="address">
    <svg viewBox="0 0 26 36" aria-hidden="true"><path d="M13 0a12 12 0 0 1 12 12c0 9-12 24-12 24S1 21 1 12A12 12 0 0 1 13 0z"/><circle cx="13" cy="12" r="4.5" fill="#fff"/></svg>
    <p>Suite 304, Level 3<br>57 Tindall<br>Street Corrandale<br>QLD 4999 Australia</p>
  </div>
</main>
</body>
</html>
```